Gift voucher for a photo shoot, folding card DIN long (21 x 9.8 cm)

Hello, I'm a professional photographer and need a new design for my gift voucher card for a photo shoot. The design should be applicable to all types of photo shoots (neutral). I prefer a sophisticated design. The folded card should be printed on both sides.
My data should be included: Logo, Address: Moltkener Strße 27, 07548 Gera, Email: fotograf@tobiaswinkel.eu, Website: www.tobiaswinkel.eu Tel.: 0174 / 5839026
Updates

Please design the folding card in DIN long format (105 x 210 mm, landscape format). The card should open horizontally. Please design the front with the words "Gift voucher for you" and my logo. Please make the logo small – the words "Gift voucher" should be in the foreground.
The colors - use elegant gray with gold or white font color.
The inside should contain the words: Photo shoot for ........ worth .....€, as well as my logo.
My contact details should be on the back.

Target Market(s)

Private customer

Colors

Designer to choose only greyscale colors for use in the design.

Requirements
Must have
• Noble appearance, a gift voucher that one likes to give away, words: Gift voucher for you, photo shoot for ..., worth .......€
Nice to have
• Noble appearance of the gift voucher, a gift voucher that you like to give away
Should not have
• no pictures

```html
<!DOCTYPE html>
<html lang="en">
<head>
<meta charset="utf-8">
<title>Gift Voucher – Tobias Winkel Fotograf</title>
<link rel="stylesheet" href="https://fonts.googleapis.com/css2?family=Cinzel:wght@400;600&family=Montserrat:wght@400;500&display=swap">
<style>
  :root {
    --backdrop: #ababab;
    --paper: #ffffff;
    --ink: #050608;
    --ink-soft: #1a1a1a;
    --muted: #a3a3a3;
    --faint: #ececec;
    --on-dark: #f2f2f2;
  }
  * { margin: 0; padding: 0; box-sizing: border-box; }
  html, body { width: 1200px; height: 1200px; overflow: hidden; }
  body { background: var(--backdrop); position: relative; font-family: "Montserrat", sans-serif; }

  .card {
    position: absolute; left: 99px; width: 1008px; height: 263px;
    background: var(--paper);
    box-shadow: 0 22px 28px -14px rgba(0,0,0,0.35);
    overflow: hidden;
  }
  .card--outside { top: 298px; }
  .card--inside { top: 653px; }

  /* Outside: back panel */
  .back-panel {
    position: absolute; left: 0; top: 0; width: 504px; height: 100%;
    background: var(--ink); color: var(--on-dark); text-align: center;
  }
  .contact-icons {
    position: absolute; left: 0; right: 0; top: 166px;
    display: flex; justify-content: center; align-items: center; gap: 8px;
  }
  .contact-icons svg { width: 9px; height: 9px; }
  .contact-icons .divider { width: 1px; height: 10px; background: var(--on-dark); }
  .contact-list {
    position: absolute; left: 0; right: 0; top: 187px;
    list-style: none; font-size: 8.4px; line-height: 16.7px; letter-spacing: 0.1px;
  }

  /* Outside: front panel */
  .front-panel { position: absolute; left: 504px; top: 0; width: 504px; height: 100%; text-align: center; }
  .brand { position: absolute; left: 0; right: 0; top: 16px; }
  .brand-circle {
    width: 46px; height: 46px; margin: 0 auto; border: 2px solid var(--ink-soft); border-radius: 50%;
  }
  .brand-name {
    font-family: "Cinzel", serif; font-weight: 400; font-size: 21px; color: var(--ink-soft);
    letter-spacing: 0.5px; margin-top: 6px; line-height: 1;
  }
  .brand-role {
    font-size: 8px; letter-spacing: 3.6px; color: #777; margin-top: 2px; font-weight: 500;
  }
  .voucher-title {
    position: absolute; left: 0; right: 0; top: 165px;
    font-family: "Cinzel", serif; font-weight: 600; font-size: 57px; line-height: 1;
    color: var(--ink); letter-spacing: 0.5px;
  }
  .voucher-sub {
    position: absolute; left: 0; right: 0; top: 222px;
    font-size: 22px; letter-spacing: 4px; color: var(--muted); font-weight: 500; line-height: 1;
  }

  /* Inside */
  .inside-shade {
    position: absolute; left: 506px; top: 0; width: 502px; height: 100%;
    background: linear-gradient(90deg, rgba(0,0,0,0.05), rgba(0,0,0,0) 40%);
  }
  .faint-circle {
    position: absolute; left: 372px; top: 0; width: 263px; height: 263px;
    border: 7px solid var(--faint); border-radius: 50%;
  }
  .shoot-title {
    position: absolute; left: 87px; top: 46px;
    font-family: "Cinzel", serif; font-weight: 600; font-size: 46px; line-height: 1; color: var(--ink);
  }
  .shoot-for {
    position: absolute; left: 223px; top: 94px; width: 60px; text-align: center;
    font-size: 22px; letter-spacing: 3px; color: var(--muted); font-weight: 500; line-height: 1;
  }
  .fill-line { position: absolute; height: 0; border-top: 2px dotted #333; }
  .fill-line--name { left: 63px; top: 209px; width: 384px; }
  .fill-line--amount { left: 607px; top: 209px; width: 234px; }
  .worth-label {
    position: absolute; left: 654px; top: 45px; width: 198px; height: 42px;
    border-top: 1px solid var(--ink-soft); border-bottom: 1px solid var(--ink-soft);
    text-align: center; line-height: 40px;
    font-size: 23px; letter-spacing: 4px; color: var(--muted); font-weight: 500;
  }
  .currency {
    position: absolute; left: 839px; top: 128px;
    font-family: "Cinzel", serif; font-size: 92px; line-height: 1; color: var(--ink);
  }
</style>
</head>
<body>

<section class="card card--outside">
  <div class="back-panel">
    <div class="contact-icons">
      <svg viewBox="0 0 10 10" fill="none" stroke="#f2f2f2" stroke-width="1.2"><path d="M2 1 L4 3 L3 4 Q4.5 6 6 7 L7 6 L9 8 L8 9 Q3 8.5 1 2 Z"/></svg>
      <span class="divider"></span>
      <svg viewBox="0 0 10 10" fill="none" stroke="#f2f2f2" stroke-width="0.9"><circle cx="5" cy="5" r="4"/><ellipse cx="5" cy="5" rx="1.8" ry="4"/><path d="M1 5 H9 M1.6 3 H8.4 M1.6 7 H8.4"/></svg>
      <span class="divider"></span>
      <svg viewBox="0 0 10 10"><rect x="0.5" y="2" width="9" height="6.5" fill="#f2f2f2"/><path d="M0.5 2 L5 5.6 L9.5 2" fill="none" stroke="#050608" stroke-width="0.8"/></svg>
      <span class="divider"></span>
      <svg viewBox="0 0 10 10" fill="none" stroke="#f2f2f2" stroke-width="1"><circle cx="5" cy="3.6" r="2.4"/><path d="M5 6 V8.2 M1.5 9 H8.5"/></svg>
    </div>
    <ul class="contact-list">
      <li>0174 / 5839026</li>
      <li>www.tobiaswinkel.eu</li>
      <li>fotograf@tobiaswinkel.eu</li>
      <li>Moltkener Strße 27, 07548 Gera</li>
    </ul>
  </div>

  <div class="front-panel">
    <div class="brand">
      <div class="brand-circle"></div>
      <p class="brand-name">Tobias Winkel</p>
      <p class="brand-role">FOTOGRAF</p>
    </div>
    <h1 class="voucher-title">Gift Voucher</h1>
    <p class="voucher-sub">FOR YOU</p>
  </div>
</section>

<section class="card card--inside">
  <div class="inside-shade"></div>
  <div class="faint-circle"></div>
  <h2 class="shoot-title">Photo Shoot</h2>
  <p class="shoot-for">FOR</p>
  <div class="fill-line fill-line--name"></div>
  <p class="worth-label">WORTH</p>
  <div class="fill-line fill-line--amount"></div>
  <span class="currency">€</span>
</section>

</body>
</html>
```